Brimora - Nutritious Snacks and Desserts

We need a creative e-commerce website in which all features--buttons, background, etc.--convey our message: We sell delicious, nutritious snacks and desserts that most closely comply with the paleo diet guidelines. Our first product is Nuttaree®--raw, vegan, paleo chocolate balls that are made of dates, coconut, and cocoa. Our products are organic, raw, irresistible and nutritious. We have several versions of Nuttaree® in development, as well as mousse, ice cream, and crackers. Our mission is to purvey basic healthy foods. Our motto is, "Fuel for the Bold Trail-Walker(tm)."

Target Market(s)

Health-conscious professionals who tend to shop at health food stores. Our products also meet the requirements of a gluten-free diet; and they also don't contain refined sugar, so shoppers with gluten and possibly sugar issues are incidental customers.

Industry/Entity Type

Health Product

Coding

Number of Pages Required

5+ page

Colors

Designer to choose colors to be used in the design.

Requirements
Must have
• We need at least a home page, a products page, an about-us page, a contact page, and a shopping cart page. We would like to be able to add products on our own later. We should be able to handle some basic coding, especially if it's just a matter of copying and modifying product pages. We would also like the ability in the future to add blogging pages, allowing us to write articles about health food and healthy lifestyle, thus attracting web-traffic (SEO).
• Other features we would like to have:
• Product photo slider on the hopepage
• Back-to-top button at the bottom of the home page
• Make sure the site is mobile-compatible
• A search bar at the top of the homepage
• "Create an account" and "Previous orders"--allowing customers to see their previous orders and reorder what they purchased in the past.
Nice to have
• We would like to convey the paleo theme without actually stating it anywhere. We'll add text as necessary, according to the page layout; you can use ipsum lorem for purpose of demonstration.

```html
<!DOCTYPE html>
<html lang="en">
<head>
<meta charset="utf-8">
<title>Brimora - Nutritious Snacks and Desserts</title>
<link rel="stylesheet" href="https://fonts.googleapis.com/css2?family=Montserrat:wght@400;500;600;700&display=swap">
<style>
:root{
  --green:#66bf16;
  --green-light:#b7e07a;
  --dark:#1c1c1c;
  --footer:#202020;
  --text:#555555;
  --grey-bg:#eef0f5;
  --white:#ffffff;
  --line:#d9dce2;
  --icon:#8a8a8a;
}
*{margin:0;padding:0;box-sizing:border-box}
html,body{width:1200px;height:2483px;overflow:hidden;background:var(--white)}
body{position:relative;font-family:Arial,Helvetica,sans-serif;color:var(--text)}
.heading{font-family:"Montserrat",sans-serif}

/* header */
.site-header{position:absolute;left:0;top:0;width:1200px;height:113px;background:var(--white)}
.brand{position:absolute;display:flex;align-items:center;gap:10px;font-family:"Montserrat",sans-serif;font-weight:600;color:var(--green);white-space:nowrap}
.brand-dot{border-radius:50%;background:var(--green);flex:none}
.header-brand{left:84px;top:34px;font-size:30px}
.header-brand .brand-dot{width:40px;height:40px}
.main-nav a{position:absolute;top:52px;width:120px;margin-left:-60px;text-align:center;font-family:"Montserrat",sans-serif;font-size:12.5px;font-weight:500;color:#333;text-decoration:none;white-space:nowrap}
.main-nav a.active{color:var(--green)}
.icon-btn{position:absolute;top:35px;width:50px;height:50px;border:2px solid var(--green);border-radius:50%}
.icon-btn svg{position:absolute;left:12px;top:12px}

/* hero */
.hero{position:absolute;left:0;top:113px;width:1200px;height:518px;background:var(--dark)}
.hero-photo{position:absolute;left:0;top:0;width:680px;height:518px;background:linear-gradient(120deg,#7a8f3a 0%,#c9703f 35%,#8a5a3a 60%,#2a2a22 100%)}
.hero-brand{left:690px;top:92px;width:270px;font-size:58px;flex-direction:column;gap:14px}
.hero-brand .brand-dot{width:124px;height:124px}
.hero-tagline{position:absolute;left:520px;width:612px;top:313px;text-align:center;font-size:23px;font-weight:500;color:var(--white);white-space:nowrap}
.btn{display:inline-block;background:var(--green);color:var(--white);font-family:"Montserrat",sans-serif;font-weight:500;border-radius:3px;text-align:center;white-space:nowrap}
.hero-btn{position:absolute;left:756px;top:370px;width:143px;height:43px;line-height:43px;font-size:18px}
.dot{position:absolute;top:485px;width:17px;height:17px;border:2px solid var(--white);border-radius:50%}
.dot.on{border-color:var(--green)}

/* welcome */
.welcome{position:absolute;left:0;top:631px;width:1200px;height:213px;background:var(--green);text-align:center;color:var(--white)}
.welcome h1{position:absolute;left:0;width:1200px;top:35px;font-size:26px;font-weight:500}
.welcome .rule{position:absolute;left:557px;top:80px;width:86px;height:2px;background:var(--white)}
.welcome p{position:absolute;left:200px;width:800px;top:106px;font-size:12px;line-height:26px;white-space:nowrap}

/* features */
.feature{position:absolute;top:890px;width:300px;text-align:center}
.feature-ring{display:block;margin:0 auto}
.feature h2{margin-top:30px;font-size:20px;font-weight:600;color:var(--green)}
.feature p{margin-top:14px;font-size:13px;line-height:25.5px;color:#666}
.slide-arrow{position:absolute;top:970px}

/* featured products */
.products{position:absolute;left:0;top:1220px;width:1200px;height:476px;background:var(--grey-bg);border-top:2px solid var(--green)}
.products-tab{position:absolute;left:427px;top:-2px;width:351px;height:53px}
.products-tab svg{position:absolute;left:0;top:0}
.products-tab span{position:absolute;left:0;width:351px;top:12px;text-align:center;font-size:23px;font-weight:500;color:var(--white)}
.product-card{position:absolute;top:92px;width:242px;height:335px;background:var(--white);border:1px solid var(--line);text-align:center}
.product-image{position:absolute;left:8px;top:7px;width:224px;height:175px;border:1px solid var(--line)}
.product-price{position:absolute;left:0;width:240px;top:200px;font-size:25px;font-weight:500;color:var(--green)}
.product-name{position:absolute;left:0;width:240px;top:240px;font-size:15px;font-weight:500;color:#333}
.product-actions{position:absolute;left:0;width:240px;top:276px;display:flex;justify-content:center;gap:7px}
.action{width:34px;height:34px;border:1px solid #999;border-radius:50%;display:flex;align-items:center;justify-content:center}

/* story */
.story-title{position:absolute;left:86px;top:1770px;font-size:24px;font-weight:500;color:var(--green)}
.story-text{position:absolute;left:86px;width:570px;font-size:13px;line-height:25px;color:#555;white-space:nowrap}
.story-btn{position:absolute;left:86px;top:2057px;width:126px;height:43px;line-height:43px;font-size:15px}
.story-visual{position:absolute;left:692px;top:1735px;width:380px;height:392px;background:#f1efec}
.story-visual .pack{position:absolute;left:18px;top:24px;width:344px;height:344px;border-radius:50%;background:radial-gradient(circle at 50% 45%,#a9744a 0%,#7a4a2b 60%,#4e2e1b 100%)}

/* footer */
.site-footer{position:absolute;left:0;top:2171px;width:1200px;height:312px;background:var(--footer);color:#e6e6e6}
.footer-brand{left:116px;top:38px;font-size:40px;flex-direction:column;gap:10px;width:232px}
.footer-brand .brand-dot{width:108px;height:108px}
.footer-col{position:absolute;top:40px}
.footer-col h3{font-size:18px;font-weight:500;color:var(--white)}
.contact-list{list-style:none;margin-top:18px;font-size:12.5px}
.contact-list li{position:relative;padding-left:26px;height:30px;line-height:16px;white-space:nowrap}
.contact-list svg{position:absolute;left:0;top:1px}
.contact-list a{color:#e6e6e6}
.footer-col p{margin-top:18px;font-size:12.5px;line-height:19px;white-space:nowrap}
.newsletter-input{width:209px;height:35px;margin-top:16px;background:var(--white);color:#888;font-size:12.5px;line-height:35px;padding-left:14px}
.subscribe{margin-top:7px;width:81px;height:28px;line-height:28px;font-size:11px;font-family:Arial,Helvetica,sans-serif;border-radius:0}
.socials{display:flex;gap:7px;margin-top:18px}
.socials span{width:36px;height:36px;border:2px solid #e6e6e6;border-radius:50%}
.copyright{position:absolute;left:0;width:1200px;top:265px;text-align:center;font-size:12.5px;color:#e6e6e6}
</style>
</head>
<body>

<header class="site-header">
  <div class="brand header-brand"><span class="brand-dot"></span>Brimora</div>
  <nav class="main-nav">
    <a class="active" href="#" style="left:424px">HOME</a>
    <a href="#" style="left:525px">ABOUT US</a>
    <a href="#" style="left:642px">PRODUCTS</a>
    <a href="#" style="left:746px">NEWS</a>
    <a href="#" style="left:842px">GALLERY</a>
    <a href="#" style="left:955px">CONTACT US</a>
  </nav>
  <span class="icon-btn" style="left:1010px">
    <svg width="22" height="22" viewBox="0 0 22 22"><path d="M2 4h3l3 10h9l2-7H7" fill="none" stroke="#66bf16" stroke-width="2.2"/><circle cx="9" cy="18" r="1.8" fill="#66bf16"/><circle cx="16" cy="18" r="1.8" fill="#66bf16"/></svg>
  </span>
  <span class="icon-btn" style="left:1063px">
    <svg width="22" height="22" viewBox="0 0 22 22"><circle cx="9" cy="9" r="5.5" fill="none" stroke="#66bf16" stroke-width="2.2"/><path d="M13 13l5 5" stroke="#66bf16" stroke-width="2.4"/></svg>
  </span>
</header>

<section class="hero">
  <div class="hero-photo" role="img" aria-label="Fresh whole foods: salmon, apples, avocado, peanuts, tomatoes and greens on a dark slate"></div>
  <div class="brand hero-brand"><span class="brand-dot"></span>Brimora</div>
  <p class="hero-tagline heading">FUEL FOR THE BOLD TRAIL-WALKER ™</p>
  <span class="btn hero-btn">READ MORE</span>
  <span class="dot" style="left:568px"></span>
  <span class="dot on" style="left:591px"></span>
  <span class="dot" style="left:614px"></span>
</section>

<section class="welcome">
  <h1 class="heading">WELCOME TO BRIMORA FOODS</h1>
  <span class="rule"></span>
  <p>Our products are raw, organic, vegan, gluten-free, dairy-free, fiber-rich, nutrient-dense, antioxidant-rich<br>real foods with no preservatives, no added sugar, and no artificial or plant-based sweeteners. And they<br>are irresistibly scrumptious!</p>
</section>

<svg class="slide-arrow" style="left:40px" width="22" height="120" viewBox="0 0 22 120"><path d="M20 0L2 60l18 60" fill="none" stroke="#c8c8c8" stroke-width="1.5"/></svg>
<svg class="slide-arrow" style="left:1146px" width="22" height="120" viewBox="0 0 22 120"><path d="M2 0l18 60L2 120" fill="none" stroke="#c8c8c8" stroke-width="1.5"/></svg>

<div class="feature" style="left:107px">
  <svg class="feature-ring" width="150" height="150" viewBox="0 0 150 150" role="img" aria-label="Tomato icon for organic"><circle cx="75" cy="75" r="72" fill="none" stroke="#b7e07a" stroke-width="3"/><path d="M75 3a72 72 0 0 1 0 144" fill="none" stroke="#66bf16" stroke-width="5"/><circle cx="75" cy="75" r="42" fill="#66bf16" opacity=".85"/></svg>
  <h2 class="heading">ORGANIC</h2>
  <p>Sed ut perspiciatis unde omnis iste natus error sit voluptatem accusantium doloremque laudantium, beatae vitae dicta sunt explicabo.</p>
</div>
<div class="feature" style="left:451px">
  <svg class="feature-ring" width="150" height="150" viewBox="0 0 150 150" role="img" aria-label="Milk bottle and cheese icon for dairy-free"><circle cx="75" cy="75" r="72" fill="none" stroke="#b7e07a" stroke-width="3"/><path d="M75 3a72 72 0 0 1 0 144" fill="none" stroke="#66bf16" stroke-width="5"/><circle cx="75" cy="75" r="42" fill="#66bf16" opacity=".85"/></svg>
  <h2 class="heading">DAIRY-FREE</h2>
  <p>Sed ut perspiciatis unde omnis iste natus error sit voluptatem accusantium doloremque laudantium, beatae vitae dicta sunt explicabo.</p>
</div>
<div class="feature" style="left:795px">
  <svg class="feature-ring" width="150" height="150" viewBox="0 0 150 150" role="img" aria-label="Wheat ear icon for gluten-free"><circle cx="75" cy="75" r="72" fill="none" stroke="#b7e07a" stroke-width="3"/><path d="M75 3a72 72 0 0 1 0 144" fill="none" stroke="#66bf16" stroke-width="5"/><circle cx="75" cy="75" r="42" fill="#66bf16" opacity=".85"/></svg>
  <h2 class="heading">GLUTEN-FREE</h2>
  <p>Sed ut perspiciatis unde omnis iste natus error sit voluptatem accusantium doloremque laudantium, beatae vitae dicta sunt explicabo.</p>
</div>

<section class="products">
  <div class="products-tab">
    <svg width="351" height="53" viewBox="0 0 351 53"><path d="M0 0h351c-20 0-26 53-60 53H60C26 53 20 0 0 0z" fill="#66bf16"/></svg>
    <span class="heading">FEATURED PRODUCTS</span>
  </div>

  <div class="product-card" style="left:86px">
    <div class="product-image" role="img" aria-label="Broken dark chocolate bar pieces" style="background:linear-gradient(135deg,#fff 20%,#5a2f1d 45%,#3b1d10 70%,#fff 90%)"></div>
    <div class="product-price heading">$ 59.00</div>
    <div class="product-name heading">CHOCOLATE</div>
    <div class="product-actions">
      <span class="action"><svg width="16" height="16" viewBox="0 0 16 16"><path d="M1 3h2l2 7h7l2-5H4" fill="none" stroke="#8a8a8a" stroke-width="1.3"/><circle cx="6" cy="13" r="1.1" fill="#8a8a8a"/><circle cx="11" cy="13" r="1.1" fill="#8a8a8a"/></svg></span>
      <span class="action"><svg width="16" height="16" viewBox="0 0 16 16"><path d="M8 13.5S2 9.5 2 5.8A3 3 0 0 1 8 4.5a3 3 0 0 1 6 1.3c0 3.7-6 7.7-6 7.7z" fill="none" stroke="#8a8a8a" stroke-width="1.3"/></svg></span>
      <span class="action"><svg width="16" height="16" viewBox="0 0 16 16"><path d="M2 5.5h11M10 3l3 2.5L10 8M14 10.5H3M6 8l-3 2.5L6 13" fill="none" stroke="#8a8a8a" stroke-width="1.3"/></svg></span>
    </div>
  </div>
  <div class="product-card" style="left:348px">
    <div class="product-image" role="img" aria-label="Swirl of chocolate mousse" style="background:radial-gradient(circle at 50% 50%,#a0705a 0%,#b88b76 28%,#fff 50%)"></div>
    <div class="product-price heading">$ 59.00</div>
    <div class="product-name heading">MOUSSE</div>
    <div class="product-actions">
      <span class="action"><svg width="16" height="16" viewBox="0 0 16 16"><path d="M1 3h2l2 7h7l2-5H4" fill="none" stroke="#8a8a8a" stroke-width="1.3"/><circle cx="6" cy="13" r="1.1" fill="#8a8a8a"/><circle cx="11" cy="13" r="1.1" fill="#8a8a8a"/></svg></span>
      <span class="action"><svg width="16" height="16" viewBox="0 0 16 16"><path d="M8 13.5S2 9.5 2 5.8A3 3 0 0 1 8 4.5a3 3 0 0 1 6 1.3c0 3.7-6 7.7-6 7.7z" fill="none" stroke="#8a8a8a" stroke-width="1.3"/></svg></span>
      <span class="action"><svg width="16" height="16" viewBox="0 0 16 16"><path d="M2 5.5h11M10 3l3 2.5L10 8M14 10.5H3M6 8l-3 2.5L6 13" fill="none" stroke="#8a8a8a" stroke-width="1.3"/></svg></span>
    </div>
  </div>
  <div class="product-card" style="left:609px">
    <div class="product-image" role="img" aria-label="Ice cream sundae in a tall glass" style="background:linear-gradient(180deg,#fff 5%,#efe6da 30%,#5a3322 55%,#d9d9d9 80%,#fff 95%)"></div>
    <div class="product-price heading">$ 59.00</div>
    <div class="product-name heading">ICE CREAM</div>
    <div class="product-actions">
      <span class="action"><svg width="16" height="16" viewBox="0 0 16 16"><path d="M1 3h2l2 7h7l2-5H4" fill="none" stroke="#8a8a8a" stroke-width="1.3"/><circle cx="6" cy="13" r="1.1" fill="#8a8a8a"/><circle cx="11" cy="13" r="1.1" fill="#8a8a8a"/></svg></span>
      <span class="action"><svg width="16" height="16" viewBox="0 0 16 16"><path d="M8 13.5S2 9.5 2 5.8A3 3 0 0 1 8 4.5a3 3 0 0 1 6 1.3c0 3.7-6 7.7-6 7.7z" fill="none" stroke="#8a8a8a" stroke-width="1.3"/></svg></span>
      <span class="action"><svg width="16" height="16" viewBox="0 0 16 16"><path d="M2 5.5h11M10 3l3 2.5L10 8M14 10.5H3M6 8l-3 2.5L6 13" fill="none" stroke="#8a8a8a" stroke-width="1.3"/></svg></span>
    </div>
  </div>
  <div class="product-card" style="left:871px">
    <div class="product-image" role="img" aria-label="Stack of square golden crackers" style="background:linear-gradient(135deg,#fff 15%,#e9a94e 40%,#d98d30 65%,#fff 88%)"></div>
    <div class="product-price heading">$ 59.00</div>
    <div class="product-name heading">CRACKERS</div>
    <div class="product-actions">
      <span class="action"><svg width="16" height="16" viewBox="0 0 16 16"><path d="M1 3h2l2 7h7l2-5H4" fill="none" stroke="#8a8a8a" stroke-width="1.3"/><circle cx="6" cy="13" r="1.1" fill="#8a8a8a"/><circle cx="11" cy="13" r="1.1" fill="#8a8a8a"/></svg></span>
      <span class="action"><svg width="16" height="16" viewBox="0 0 16 16"><path d="M8 13.5S2 9.5 2 5.8A3 3 0 0 1 8 4.5a3 3 0 0 1 6 1.3c0 3.7-6 7.7-6 7.7z" fill="none" stroke="#8a8a8a" stroke-width="1.3"/></svg></span>
      <span class="action"><svg width="16" height="16" viewBox="0 0 16 16"><path d="M2 5.5h11M10 3l3 2.5L10 8M14 10.5H3M6 8l-3 2.5L6 13" fill="none" stroke="#8a8a8a" stroke-width="1.3"/></svg></span>
    </div>
  </div>
</section>

<h2 class="story-title heading">SELL NUTRITIOUS SNACKS</h2>
<p class="story-text" style="top:1822px">Sed ut perspiciatis unde omnis iste natus error sit voluptatem accusantium doloremque laudantium,<br>totam rem aperiam, eaque ipsa quae ab illo inventore veritatis et quasi architecto beatae vitae dicta<br>sunt explicabo. Nemo enim ipsam voluptatem quia voluptas sit aspernatur aut odit aut fugit, sed quia<br>consequuntur magni dolores eos qui ratione voluptatem sequi nesciunt.</p>
<p class="story-text" style="top:1949px">Sed ut perspiciatis unde omnis iste natus error sit voluptatem accusantium doloremque laudantium,<br>totam rem aperiam, eaque ipsa quae ab illo inventore veritatis et quasi architecto beatae vitae dicta<br>sunt explicabo. Nemo enim ipsam voluptatem quia voluptas sit aspernatur</p>
<span class="btn story-btn">READ MORE</span>
<div class="story-visual" role="img" aria-label="Round Nuttaree® chocolate ball package label with a taste gauge">
  <div class="pack"></div>
</div>

<footer class="site-footer">
  <div class="brand footer-brand"><span class="brand-dot"></span>Brimora</div>

  <div class="footer-col" style="left:404px">
    <h3>CONTACT US</h3>
    <ul class="contact-list">
      <li><svg width="14" height="14" viewBox="0 0 14 14"><path d="M1 5c0-3 12-3 12 0l-2 1-1-2H4L3 6zM3 7h8l2 6H1z" fill="#e6e6e6"/></svg>(000)-121-1231 &nbsp;(Phone)</li>
      <li><svg width="14" height="14" viewBox="0 0 14 14"><path d="M3 1h8v4H3zM1 5h12v6h-2v2H3v-2H1z" fill="#e6e6e6"/></svg>(000)-121-1231 &nbsp;&nbsp;&nbsp;&nbsp;(Fax)</li>
      <li><svg width="14" height="14" viewBox="0 0 14 14"><path d="M1 3h12v8H1z" fill="#e6e6e6"/><path d="M1 3l6 5 6-5" fill="none" stroke="#202020" stroke-width="1.2"/></svg><a href="#">info@brimora.com</a></li>
      <li><svg width="14" height="14" viewBox="0 0 14 14"><path d="M7 1a4 4 0 0 1 4 4c0 3-4 8-4 8S3 8 3 5a4 4 0 0 1 4-4z" fill="#e6e6e6"/><circle cx="7" cy="5" r="1.5" fill="#202020"/></svg># 2564 Lorem Ipsum Dummy<br>Lorem Ipsum Dummy</li>
    </ul>
  </div>

  <div class="footer-col" style="left:637px">
    <h3>NEWSLETTER</h3>
    <p>Register Your email address to get<br>information ablout us</p>
    <div class="newsletter-input">Email Address</div>
    <div class="btn subscribe">SUBSCRIBE</div>
  </div>

  <div class="footer-col" style="left:902px">
    <h3>FOLLOW US</h3>
    <p>Lorem ipsum dolor sit amet, conse<br>ctetur adipiscing elit. Nulla in purus<br>nibh. Donec ornare</p>
    <div class="socials"><span></span><span></span><span></span><span></span><span></span></div>
  </div>

  <p class="copyright">© Copyright 2018 Brimora.All Rights Reserved</p>
</footer>

</body>
</html>
```